Marlow Sail Works President Business Card Carbon fiber catamarans

Hi.. I need a new business card design.. I am the President of a high tech yacht builder. We build Carbon Fiber go fast catamarans... Maybe we use the file I am sharing to you as the back of the card.. We need to look cool and crisp ...

Target Market(s)

Affluent People who will purchase a cool yacht

Industry/Entity Type

Custom Yacht Builder

Contact Information for Business Card

Dean Pellway , President, 731.508.2164 USA

Font styles to use
Serif

Requirements
Must have
• the clean crisp cool feel
Nice to have
• clean and crisp
Should not have
• Bold ugly

```html
<!DOCTYPE html>
<html lang="en">
<head>
<meta charset="utf-8">
<title>Marlow Sail Works – Business Card</title>
<link rel="stylesheet" href="https://fonts.googleapis.com/css2?family=Michroma&family=Montserrat:wght@400;500&display=swap">
<style>
  :root {
    --stage: #3a3b3d;
    --card: #141516;
    --carbon-dark: #0d0e0f;
    --carbon-mid: #1d1e20;
    --silver: #d9dbdd;
    --silver-soft: #a9acaf;
    --white: #f2f3f4;
  }
  * { box-sizing: border-box; margin: 0; padding: 0; }
  html, body { width: 1200px; height: 801px; overflow: hidden; }
  body {
    background: var(--stage);
    font-family: "Montserrat", sans-serif;
    position: relative;
  }
  .card {
    position: absolute;
    top: 252px;
    width: 520px;
    height: 297px;
    border-radius: 18px;
    overflow: hidden;
    box-shadow: 0 14px 30px rgba(0,0,0,0.45);
  }
  .card--back { left: 50px; }
  .card--front { left: 630px; background: var(--card); }

  .carbon-texture {
    position: absolute; inset: 0;
    background: radial-gradient(ellipse at 40% 35%, var(--carbon-mid), var(--carbon-dark) 75%);
  }
  .brand {
    font-family: "Michroma", sans-serif;
    color: var(--silver);
    font-weight: 400;
    text-transform: uppercase;
    display: flex;
    align-items: center;
    line-height: 1.25;
  }
  .brand-dot {
    border-radius: 50%;
    background: var(--silver);
    flex: none;
  }
  .brand-name span { display: block; }

  .card--back .brand {
    position: absolute;
    left: 0; right: 0; top: 82px;
    justify-content: center;
    gap: 16px;
    font-size: 24px;
    letter-spacing: 3px;
  }
  .card--back .brand-dot { width: 36px; height: 36px; }
  .card--back .website {
    position: absolute;
    left: 0; right: 0; top: 196px;
    text-align: center;
    font-size: 11px;
    letter-spacing: 3px;
    color: var(--silver-soft);
    text-transform: uppercase;
  }

  .card--front .brand {
    position: absolute;
    left: 34px; top: 38px;
    gap: 10px;
    font-size: 14px;
    letter-spacing: 2px;
  }
  .card--front .brand-dot { width: 24px; height: 24px; }
  .person {
    position: absolute;
    right: 36px; top: 40px;
    text-align: right;
  }
  .person-name {
    font-family: "Michroma", sans-serif;
    font-size: 16px;
    letter-spacing: 2px;
    color: var(--silver);
    text-transform: uppercase;
  }
  .person-role {
    margin-top: 6px;
    font-size: 10px;
    letter-spacing: 1.5px;
    color: var(--silver-soft);
  }
  .contacts {
    position: absolute;
    left: 34px; bottom: 32px;
    list-style: none;
  }
  .contacts li {
    display: flex;
    align-items: center;
    gap: 8px;
    font-size: 12px;
    letter-spacing: 2px;
    color: var(--white);
    text-transform: uppercase;
    margin-top: 9px;
  }
  .contacts svg { width: 12px; height: 12px; fill: var(--silver); flex: none; }
</style>
</head>
<body>
  <section class="card card--back">
    <div class="carbon-texture" role="img" aria-label="Carbon fiber weave texture"></div>
    <div class="brand">
      <span class="brand-dot"></span>
      <p class="brand-name"><span>Marlow</span><span>Sail Works</span></p>
    </div>
    <p class="website">www.marlowsailworks.com</p>
  </section>

  <section class="card card--front">
    <div class="brand">
      <span class="brand-dot"></span>
      <p class="brand-name"><span>Marlow</span><span>Sail Works</span></p>
    </div>
    <div class="person">
      <p class="person-name">Dean Pellway</p>
      <p class="person-role">President</p>
    </div>
    <ul class="contacts">
      <li>
        <svg viewBox="0 0 24 24" aria-hidden="true"><path d="M6.6 10.8a15.1 15.1 0 0 0 6.6 6.6l2.2-2.2a1 1 0 0 1 1-.25 11.4 11.4 0 0 0 3.6.57 1 1 0 0 1 1 1V20a1 1 0 0 1-1 1A17 17 0 0 1 3 4a1 1 0 0 1 1-1h3.5a1 1 0 0 1 1 1c0 1.25.2 2.45.57 3.57a1 1 0 0 1-.25 1z"/></svg>
        731.508.2164
      </li>
      <li>
        <svg viewBox="0 0 24 24" aria-hidden="true"><path d="M2 5h20v14H2z M2 5l10 8 10-8" fill="none" stroke="#d9dbdd" stroke-width="2"/></svg>
        info@marlowsail.com
      </li>
      <li>
        <svg viewBox="0 0 24 24" aria-hidden="true"><circle cx="12" cy="12" r="9" fill="none" stroke="#d9dbdd" stroke-width="2"/><path d="M3 12h18M12 3c3 3 3 15 0 18M12 3c-3 3-3 15 0 18" fill="none" stroke="#d9dbdd" stroke-width="1.5"/></svg>
        www.marlowsail.com
      </li>
    </ul>
  </section>
</body>
</html>
```